Tidewell Homecare

I am looking to have a website designed for a housekeeping company that looks similar to this one. https://marloweshomecare.example/

I need 5 websites designed but will start with this one to see how I like it.

Industry/Entity Type

House Cleaning

Coding

Coded - Design and coding required

Number of Pages Required

5+ page

Font styles to use
Serif
Script

Colors
ffffff
fdf9cf
fbf289
fbee3f
d6edf3
86cae7
33a6d7
edf1f8
cedeed

```html
<!DOCTYPE html>
<html lang="en">
<head>
<meta charset="utf-8">
<title>Tidewell Homecare</title>
<link href="https://fonts.googleapis.com/css2?family=Montserrat:wght@400;500;600;700&family=Hind:wght@400;500;600&family=Arimo:wght@400&display=swap" rel="stylesheet">
<style>
:root{
  --white:#ffffff;
  --cream:#fdf9cf;
  --lemon:#fbee3f;
  --lemon-soft:#fbf289;
  --sky-pale:#d6edf3;
  --sky:#86cae7;
  --blue:#33a6d7;
  --blue-deep:#2a88c6;
  --mist:#edf1f8;
  --mist-dark:#cedeed;
  --ink:#1f2630;
  --text:#444c55;
  --head:"Montserrat",sans-serif;
  --body:"Hind",sans-serif;
}
*{box-sizing:border-box;margin:0;padding:0}
html,body{width:1200px;height:3410px;overflow:hidden}
body{position:relative;background:var(--white);font-family:var(--body);color:var(--text)}
.abs{position:absolute}

/* header */
.site-header{left:0;top:0;width:1200px;height:97px;background:var(--white)}
.brand{left:49px;top:31px;font-family:var(--head);font-weight:700;font-size:23px;color:var(--blue);letter-spacing:1px}
.main-nav a{position:absolute;top:37px;font-family:var(--head);font-size:16px;color:#6a7078;text-decoration:none;letter-spacing:.5px}
.main-nav a.active{color:var(--blue)}
.phone-btn{left:972px;top:21px;width:191px;height:48px;border-radius:24px;background:var(--lemon);display:flex;align-items:center;justify-content:center;gap:6px;font-family:var(--head);font-weight:700;font-size:18px;color:var(--ink)}

/* hero */
.hero{left:0;top:97px;width:1200px;height:610px;background:linear-gradient(120deg,#c9c4bc 0%,#e9e6e0 40%,#a9a39a 75%,#d9d3c8 100%)}
.hero-circle{left:106px;top:82px;width:424px;height:424px;border-radius:50%;background:rgba(51,166,215,.82);border:6px solid var(--white);text-align:center;color:var(--white)}
.hero-circle h1{margin:126px auto 0;width:360px;font-family:var(--head);font-weight:600;font-size:28px;line-height:39px;letter-spacing:1px}
.hero-circle p{margin:12px auto 0;width:310px;font-size:17px;line-height:25px}
.hero-arrow{top:250px}

/* services */
.service-card{top:796px;width:437px;height:274px;border:2px solid;text-align:center;background:var(--white)}
.service-card.commercial{left:142px;border-color:var(--lemon)}
.service-card.residential{left:619px;border-color:var(--sky)}
.service-icon{position:absolute;left:167px;top:-52px;width:102px;height:102px;border-radius:50%;background:var(--white);border:3px solid}
.commercial .service-icon{border-color:var(--lemon)}
.residential .service-icon{border-color:var(--sky)}
.service-card h2{margin-top:74px;font-family:var(--head);font-weight:400;font-size:21px;letter-spacing:1.5px;color:var(--ink)}
.service-card p{margin:14px auto 0;width:380px;font-size:15px;line-height:24px}
.pill{display:inline-block;margin-top:16px;width:166px;height:49px;line-height:51px;border-radius:25px;font-family:var(--head);font-weight:700;font-size:13px;letter-spacing:.5px}
.commercial .pill{background:var(--lemon);color:var(--ink)}
.residential .pill{background:var(--blue);color:var(--white)}

/* about */
.about-panel{left:0;top:1131px;width:603px;height:478px;background:linear-gradient(135deg,var(--blue) 0%,#5fb3e0 100%);text-align:center;color:var(--white)}
.about-panel h2{margin-top:86px;font-family:var(--head);font-weight:600;font-size:25px;letter-spacing:1px;line-height:30px}
.about-panel h2 span{display:block;font-size:38px;line-height:44px;font-weight:700;letter-spacing:2px}
.about-panel p{margin:20px auto 0;width:500px;font-size:16px;line-height:25px}
.about-panel .learn{display:inline-block;margin-top:30px;width:157px;height:48px;line-height:50px;border-radius:24px;background:var(--mist);color:var(--blue);font-family:var(--head);font-weight:700;font-size:13px}
.about-photo{left:603px;top:1131px;width:597px;height:478px;background:linear-gradient(160deg,#e8e6e2 0%,#bdbab4 55%,#6b4c36 100%)}

/* work */
.section-title{width:1200px;left:0;text-align:center;font-family:var(--head);font-weight:700;font-size:29px;letter-spacing:1.5px;color:var(--ink)}
.work-tile{width:362px;height:235px}

/* testimonials */
.testimonials{left:0;top:2267px;width:1200px;height:503px;background:var(--lemon)}
.testimonial-photo{left:0;top:0;width:503px;height:503px;background:linear-gradient(135deg,#38b8c9 0%,#7fd6a0 35%,var(--lemon) 70%,var(--lemon) 100%)}
.testimonials h2{left:551px;top:102px;font-family:var(--head);font-weight:700;font-size:29px;letter-spacing:2px;color:var(--ink)}
.quote{left:552px;top:168px;width:530px;font-family:"Arimo",sans-serif;font-size:20px;line-height:31.5px;color:var(--ink)}
.qmark{font-family:Georgia,serif;font-weight:700;font-size:62px;color:var(--ink);line-height:1}
.qmark-close{display:inline-block;vertical-align:-26px;margin-left:6px;font-family:Georgia,serif;font-weight:700;font-size:62px;line-height:20px;color:var(--ink)}
.author{left:553px;top:342px;font-family:var(--head);font-weight:700;font-size:17px;letter-spacing:1px;color:var(--ink)}
.dots{left:553px;top:396px;display:flex;gap:9px}
.dots span{width:13px;height:13px;border-radius:50%;background:#7a6d2a}
.dots span.on{background:transparent;border:2px solid #7a6d2a}

/* estimate */
.estimate{left:0;top:2770px;width:1200px;height:476px;background:linear-gradient(90deg,var(--mist) 0%,#f5f7fb 50%,var(--sky-pale) 100%)}
.estimate p{left:0;width:1200px;top:134px;text-align:center;font-size:14px;line-height:23px;color:#6a7078}
.field{height:49px;width:249px;background:var(--white);border:1px solid var(--mist-dark);font-size:14px;color:var(--ink);padding:17px 0 0 16px}
.submit{left:522px;top:349px;width:163px;height:50px;border-radius:25px;background:var(--blue);color:var(--white);text-align:center;line-height:52px;font-family:var(--head);font-weight:700;font-size:18px;letter-spacing:1.5px}

/* footer */
.site-footer{left:0;top:3246px;width:1200px;height:164px;background:var(--blue-deep);color:var(--white)}
.foot-nav a{position:absolute;top:62px;color:var(--white);font-family:var(--head);font-size:13px;text-decoration:none;letter-spacing:.3px}
.copy{left:126px;top:99px;font-family:var(--head);font-size:12px}
.contact-lines{left:771px;top:60px;font-family:var(--head);font-size:14px;line-height:25px}
.social{top:47px;width:30px;height:30px;border-radius:50%;border:2px solid var(--white)}
</style>
</head>
<body>

<header class="site-header abs">
  <div class="brand abs">TIDEWELL HOMECARE</div>
  <nav class="main-nav">
    <a class="active" style="left:401px">SERVICES</a>
    <a style="left:526px">ABOUT</a>
    <a style="left:629px">REVIEWS</a>
    <a style="left:751px">BLOGS</a>
    <a style="left:852px">CONTACT</a>
  </nav>
  <div class="phone-btn abs">
    <svg width="16" height="16" viewBox="0 0 24 24"><path fill="#1f2630" d="M6.6 10.8a15.1 15.1 0 0 0 6.6 6.6l2.2-2.2c.3-.3.7-.4 1-.2 1.1.4 2.3.6 3.6.6.6 0 1 .4 1 1V20c0 .6-.4 1-1 1A17 17 0 0 1 3 4c0-.6.4-1 1-1h3.5c.6 0 1 .4 1 1 0 1.3.2 2.5.6 3.6.1.3 0 .7-.2 1z"/></svg>
    555-310-4172
  </div>
</header>

<section class="hero abs" role="img" aria-label="Bright modern living room with grey sofa and open kitchen">
  <svg class="abs hero-arrow" style="left:22px" width="26" height="40" viewBox="0 0 26 40"><path d="M22 3 5 20l17 17" stroke="#fff" stroke-width="4" fill="none"/></svg>
  <svg class="abs hero-arrow" style="left:1140px" width="26" height="40" viewBox="0 0 26 40"><path d="M4 3l17 17L4 37" stroke="#fff" stroke-width="4" fill="none"/></svg>
  <div class="hero-circle abs">
    <h1>WELCOME TO<br>TIDEWELL HOMECARE</h1>
    <p>Lorem ipsum dolor sit amet consect etuer adipiscing elit Nam cursus Morbi ut mi Nullam enim</p>
    <svg style="margin-top:14px" width="34" height="20" viewBox="0 0 34 20"><path d="M3 3l14 14L31 3" stroke="#fff" stroke-width="4" fill="none"/></svg>
  </div>
</section>

<article class="service-card commercial abs">
  <div class="service-icon">
    <svg width="96" height="96" viewBox="0 0 96 96" fill="none" stroke="#f5d800" stroke-width="2.5"><rect x="28" y="24" width="24" height="16"/><path d="M36 40v6h8v-6M24 50h50M28 50v22M70 50v22M28 60h20v12M56 56h12M56 50v12"/></svg>
  </div>
  <h2>COMMERCIAL CLEANING</h2>
  <p>Augiat in pede Fusce tellus Sed metus augue convallis et vehicula ut pulvinar eu ante Integer orci tellus tristique vitae consequat nec</p>
  <span class="pill">VIEW SERVICES</span>
</article>

<article class="service-card residential abs">
  <div class="service-icon">
    <svg width="96" height="96" viewBox="0 0 96 96" fill="none" stroke="#33a6d7" stroke-width="2.5"><path d="M26 46V34c0-4 3-6 6-6h32c3 0 6 2 6 6v12"/><path d="M20 46h56v14H20zM26 60v6M70 60v6M48 30v16"/><circle cx="38" cy="36" r="1.5"/><circle cx="58" cy="36" r="1.5"/></svg>
  </div>
  <h2>RESIDENTIAL CLEANING</h2>
  <p>Augiat in pede Fusce tellus Sed metus augue convallis et vehicula ut pulvinar eu ante Integer orci tellus tristique vitae consequat nec</p>
  <span class="pill">VIEW SERVICES</span>
</article>

<section class="about-panel abs">
  <h2>ABOUT TIDEWELL <span>HOMECARE</span></h2>
  <p>Augiat in pede Fusce tellus Sed metus augue convallis et vehicula ut pulvinar eu ante Integer orci tellus tristique vitae consequat nec mauris viverra in gravida eu mattis in ante Morbi eget arcurmentum vel congue id euismod in elit Fusce ultricies orci ac feugiat suscipit leo massa sodales velit et scelerisque mi tortor at ipsum Proin orci odio commodo ac gravida non tristique vel te Curabitur iaculis</p>
  <span class="learn">LEARN MORE</span>
</section>
<div class="about-photo abs" role="img" aria-label="White kitchen with marble island and steel appliances"></div>

<h2 class="section-title abs" style="top:1654px">OUR WORK</h2>
<div class="work-tile abs" style="left:48px;top:1722px;background:linear-gradient(160deg,#e4e2de,#9a8a78)" role="img" aria-label="Clean kitchen with island and bar stools"></div>
<div class="work-tile abs" style="left:420px;top:1722px;background:linear-gradient(180deg,#f1f0ec,#d8d6d0)" role="img" aria-label="Carpet being steam cleaned"></div>
<div class="work-tile abs" style="left:796px;top:1722px;background:linear-gradient(160deg,#f3f2ef,#a08a72)" role="img" aria-label="Open kitchen and dining room"></div>
<div class="work-tile abs" style="left:48px;top:1968px;background:linear-gradient(160deg,#d9884a,#c9bfa8)" role="img" aria-label="Living room with sofa and cushions"></div>
<div class="work-tile abs" style="left:420px;top:1968px;background:linear-gradient(180deg,#dfe6ec,#9aa3ab)" role="img" aria-label="Bright open office with desks"></div>
<div class="work-tile abs" style="left:796px;top:1968px;background:linear-gradient(180deg,#e2e3e1,#b7b8b5)" role="img" aria-label="Grey sofa in minimal room"></div>

<section class="testimonials abs">
  <div class="testimonial-photo abs" role="img" aria-label="Cleaning gloves, sponges, brush and spray bottle"></div>
  <h2 class="abs">TESTIMONIALS</h2>
  <div class="abs" style="left:510px;top:160px"><span class="qmark">&ldquo;</span></div>
  <p class="quote abs">Augiat in pede Fusce tellus Sed metus augue convallis et vehicula ut pulvinar eu ante Integer orci tellus tristique vitae consequat nec mauris viverra in gravida eu mattis in ante Morbi eget arcurmentum vel congue id euismod in elit Fusce ultricies orci ac feugiat suscipit leo!<span class="qmark-close">&rdquo;</span></p>
  <div class="author abs">BY AUTHOR NAME</div>
  <div class="dots abs"><span class="on"></span><span></span><span></span><span></span></div>
</section>

<section class="estimate abs">
  <h2 class="section-title abs" style="top:80px">FREE ESTIMATE</h2>
  <p class="abs">Augiat in pede Fusce tellus Sed metus augue convallis et vehicula ut pulvinar eu ante Integer orci tellus tristique vitae<br>consequat nec mauris viverra in gravida eu mattis in ante Morbi eget arcurmentu</p>
  <div class="field abs" style="left:93px;top:198px">Name *</div>
  <div class="field abs" style="left:354px;top:198px">Email *</div>
  <div class="field abs" style="left:615px;top:198px">City *</div>
  <div class="field abs" style="left:873px;top:198px">Area Sq ft *</div>
  <div class="field abs" style="left:93px;top:264px">Property Type*</div>
  <div class="field abs" style="left:354px;top:264px">Type of Cleaning*</div>
  <div class="field abs" style="left:615px;top:264px">Select Date*</div>
  <div class="field abs" style="left:873px;top:264px">Select Time*</div>
  <div class="submit abs">SUBMIT</div>
</section>

<footer class="site-footer abs">
  <nav class="foot-nav">
    <a style="left:126px">HOME</a>
    <a style="left:178px">SERVICES</a>
    <a style="left:290px">ABOUT</a>
    <a style="left:420px">REVIEWS</a>
    <a style="left:531px">BLOGS</a>
    <a style="left:622px">CONTACT</a>
  </nav>
  <div class="copy abs">© 2020 Company Name | All Rights Reserved</div>
  <svg class="abs" style="left:750px;top:62px" width="14" height="18" viewBox="0 0 14 18"><path fill="#fff" d="M7 0a7 7 0 0 0-7 7c0 5 7 11 7 11s7-6 7-11a7 7 0 0 0-7-7zm0 10a3 3 0 1 1 0-6 3 3 0 0 1 0 6z"/></svg>
  <svg class="abs" style="left:750px;top:113px" width="14" height="14" viewBox="0 0 24 24"><path fill="#fff" d="M6.6 10.8a15.1 15.1 0 0 0 6.6 6.6l2.2-2.2c.3-.3.7-.4 1-.2 1.1.4 2.3.6 3.6.6.6 0 1 .4 1 1V20c0 .6-.4 1-1 1A17 17 0 0 1 3 4c0-.6.4-1 1-1h3.5c.6 0 1 .4 1 1 0 1.3.2 2.5.6 3.6.1.3 0 .7-.2 1z"/></svg>
  <div class="contact-lines abs">48 Harbor Lane #B<br>Texas 75001 TX<br>(555) 284 6630</div>
  <div class="social abs" style="left:973px"></div>
  <div class="social abs" style="left:1009px"></div>
  <div class="social abs" style="left:1045px"></div>
</footer>

</body>
</html>
```